Business Card Design - VNT (company name)

Over 20 years of progressive technology design, migration and management experience that drives business objectives and streamlines operations. Continuously challenge conventions to meet and exceed business security, availability and functionality requirements. Maintain exceptional vendor relationships to ensure ongoing knowledge of emerging products and to secure preferred service agreements. Recruit and utilize top talent and foster a collegial environment that advances innovation and performance excellence. design logo using 3 arrows of different colors green, gold, blue

Industry/Entity Type

Progressive

Contact Information for Business Card

Martin K. Osgood
IT Strategist / Consultant

626.583.2907 MOsgood@vntosgood.example 4817 Brenning Court Pasadena, CA 91104

Colors
0255a3
f37122
fece3e

Requirements
Must have
• Note NEW EMAIL ADDRESS
• MOsgood@vntosgood.example
• NOTE NEW ORDER of the work I do.
• Infrastructure – Systems – Cybersecurity
Nice to have
• main color should be orange

```html
<!DOCTYPE html>
<html lang="en">
<head>
<meta charset="utf-8">
<title>VNT Business Card</title>
<link rel="stylesheet" href="https://fonts.googleapis.com/css2?family=Lato:wght@400;700&family=Arimo&family=PT+Sans&display=swap">
<style>
  :root {
    --backdrop: #2b2d2e;
    --card-front: #eceeee;
    --card-back: #dde1e0;
    --ink-dark: #3c4444;
    --ink-mid: #5f6869;
    --ink-body: #2a2a2a;
    --accent-blue: #3a78f2;
    --accent-green: #4fdc00;
    --accent-orange: #ffa000;
    --brand-grey: #666f70;
  }
  * { margin: 0; padding: 0; box-sizing: border-box; }
  html, body { width: 1200px; height: 864px; overflow: hidden; }
  body { background: var(--backdrop); position: relative; }

  .card {
    position: absolute;
    width: 576px;
    height: 346px;
    box-shadow: 0 2px 6px rgba(0,0,0,0.35);
  }
  .card--front { left: 314px; top: 73px; background: var(--card-front); }
  .card--back { left: 313px; top: 459px; height: 340px; background: var(--card-back); }

  .holder { position: absolute; left: 52px; top: 54px; font-family: "Lato", sans-serif; }
  .holder__name { font-size: 25px; font-weight: 700; color: var(--ink-dark); line-height: 1.1; }
  .holder__title { font-size: 17px; color: var(--ink-mid); margin-top: 3px; }

  .contact { position: absolute; left: 52px; top: 188px; font-family: "Arimo", sans-serif; font-size: 15px; line-height: 20px; }
  .contact__label { display: block; }
  .contact__label--phone { color: var(--accent-blue); }
  .contact__label--email { color: var(--accent-green); }
  .contact__label--address { color: var(--accent-orange); }
  .contact__value { display: block; color: var(--ink-body); }

  .brand { position: absolute; display: flex; align-items: center; font-family: "Lato", sans-serif; font-weight: 700; color: var(--brand-grey); }
  .brand__mark { background: var(--accent-orange); border-radius: 50%; }
  .brand--front { left: 318px; top: 118px; gap: 16px; font-size: 58px; }
  .brand--front .brand__mark { width: 44px; height: 44px; }
  .brand--back { left: 0; right: 0; top: 92px; justify-content: center; gap: 22px; font-size: 84px; }
  .brand--back .brand__mark { width: 62px; height: 62px; }

  .services { position: absolute; left: 0; right: 0; top: 259px; text-align: center; font-family: "PT Sans", sans-serif; font-size: 16px; color: var(--ink-mid); letter-spacing: 0.1px; }
  .services__sep { margin: 0 4px; }
</style>
</head>
<body>
  <section class="card card--front">
    <div class="holder">
      <p class="holder__name">Martin K. Osgood</p>
      <p class="holder__title">Managing Director</p>
    </div>
    <div class="contact">
      <span class="contact__label contact__label--phone">telephone</span>
      <span class="contact__value">626.583.2907</span>
      <span class="contact__label contact__label--email">email</span>
      <span class="contact__value">MOsgood@vntosgood.example</span>
      <span class="contact__label contact__label--address">address</span>
      <span class="contact__value">4817 Brenning Court</span>
    </div>
    <div class="brand brand--front">
      <span class="brand__mark"></span>
      <span class="brand__name">VNT</span>
    </div>
  </section>

  <section class="card card--back">
    <div class="brand brand--back">
      <span class="brand__mark"></span>
      <span class="brand__name">VNT</span>
    </div>
    <p class="services">IT Strategist<span class="services__sep">|</span>ConsultantSystems<span class="services__sep">|</span>Infrastructure<span class="services__sep">|</span>Cybersecurity</p>
  </section>
</body>
</html>
```